Business card design Needed for new logo / Construction business, home extensions and new builds

We need a business card design using our new logo files which i will attach to this project :)

We are a small construction business specialising in home extensions, new builds and property development. We are very ambitious and would appreciate professional and elegant designs for our new business card.

Very serious about using the services on MakerQuarry and recently acquired our new logo from here :)

Please get involved, i will feedback when i can as i am very busy but can respond daily, thanks

Target Market(s)

People that want to build onto their houses, new building developments or adding too their existing property

Industry/Entity Type

Construction

Contact Information for Business Card

Renwick Tolliver Construction, Lionel Ashby (Managing Director), Tel 07822254961, email - info@renwick-tolliver, www.renwick-tolliver.co.uk

Colors

Designer to choose colors to be used in the design.

Requirements
Must have
• I like a deep grey on the back please. A lot of you have provided black from and back, try mixing things up a little. The black looks cool 😎 Thanks

```html
<!DOCTYPE html>
<html lang="en">
<head>
<meta charset="utf-8">
<title>Renwick Tolliver Construction – Business Card</title>
<link rel="stylesheet" href="https://fonts.googleapis.com/css2?family=Open+Sans:wght@400;600;700&display=swap">
<style>
  :root {
    --stage: #232325;
    --card-back: #2a2a2e;
    --card-front: #1d1d20;
    --panel-top: #26262a;
    --panel-mid: #212124;
    --gold: #d9a12e;
    --gold-deep: #b8801c;
    --silver: #c9c9cc;
    --white: #f4f4f4;
    --emboss: #38383d;
  }
  * { box-sizing: border-box; margin: 0; padding: 0; }
  html, body {
    width: 1200px; height: 780px; overflow: hidden;
    background: var(--stage);
    font-family: "Open Sans", Arial, sans-serif;
  }
  .stage { position: relative; width: 1200px; height: 780px; }

  .card {
    position: absolute; top: 100px;
    width: 360px; height: 580px;
    border-radius: 28px; overflow: hidden;
    box-shadow: 0 18px 40px rgba(0,0,0,.55);
  }

  /* Back of card */
  .card--back { left: 180px; background: var(--card-back); }
  .back-mark {
    position: absolute; left: 0; right: 0; top: 235px;
    display: flex; flex-direction: column; align-items: center; gap: 14px;
  }
  .back-mark__dot { width: 46px; height: 46px; border-radius: 50%; background: var(--emboss); }
  .back-mark__name {
    color: var(--emboss); font-weight: 700; font-size: 22px;
    letter-spacing: 2px; text-align: center; line-height: 1.3;
    text-transform: uppercase;
  }

  /* Front of card */
  .card--front { left: 660px; background: var(--card-front); }
  .card__layers { position: absolute; inset: 0; }

  .brand {
    position: absolute; left: 0; right: 0; top: 62px;
    display: flex; flex-direction: column; align-items: center; gap: 12px;
  }
  .brand__dot { width: 40px; height: 40px; border-radius: 50%; background: var(--gold); }
  .brand__name {
    color: var(--gold); font-weight: 600; font-size: 19px;
    letter-spacing: 2px; text-align: center; line-height: 1.35;
    text-transform: uppercase;
  }

  .person { position: absolute; left: 0; right: 0; top: 218px; text-align: center; }
  .person__name { font-weight: 700; font-size: 30px; line-height: 1.1; }
  .person__first { color: var(--silver); }
  .person__last { color: var(--gold); }
  .person__title { color: var(--white); font-size: 15px; font-weight: 600; margin-top: 4px; }

  .contact-icons {
    position: absolute; left: 0; right: 0; top: 292px;
    display: flex; justify-content: center; gap: 10px;
  }
  .icon-badge {
    width: 26px; height: 26px; border-radius: 50%;
    background: linear-gradient(145deg, var(--gold), var(--gold-deep));
    display: flex; align-items: center; justify-content: center;
  }
  .icon-badge svg { width: 14px; height: 14px; }

  .contact-list {
    position: absolute; left: 0; right: 0; top: 330px;
    list-style: none; text-align: center;
    color: var(--white); font-size: 14.5px; line-height: 1.5;
  }

  .address {
    position: absolute; right: 30px; bottom: 36px;
    text-align: right; color: var(--white); font-size: 15px; line-height: 1.4;
  }
  .address .icon-badge { margin: 0 0 10px auto; width: 28px; height: 28px; }
</style>
</head>
<body>
<main class="stage">

  <section class="card card--back" aria-label="Card back">
    <div class="back-mark">
      <span class="back-mark__dot"></span>
      <p class="back-mark__name">Renwick Tolliver<br>Construction</p>
    </div>
  </section>

  <section class="card card--front" aria-label="Card front">
    <svg class="card__layers" viewBox="0 0 360 580" width="360" height="580" aria-hidden="true">
      <defs>
        <filter id="panel-shadow" x="-20%" y="-20%" width="140%" height="140%">
          <feDropShadow dx="0" dy="6" stdDeviation="8" flood-color="#000" flood-opacity=".55"/>
        </filter>
      </defs>
      <path d="M0 0 H360 V360 Q330 470 150 480 L0 480 Z" fill="var(--panel-mid)" filter="url(#panel-shadow)"/>
      <path d="M0 0 H360 V250 Q345 430 110 440 L0 440 Z" fill="var(--panel-top)" filter="url(#panel-shadow)"/>
    </svg>

    <div class="brand">
      <span class="brand__dot"></span>
      <p class="brand__name">Renwick Tolliver<br>Construction</p>
    </div>

    <div class="person">
      <p class="person__name"><span class="person__first">Lionel</span> <span class="person__last">Ashby</span></p>
      <p class="person__title">Managing Director</p>
    </div>

    <div class="contact-icons">
      <span class="icon-badge" aria-label="Phone">
        <svg viewBox="0 0 24 24"><path fill="#1d1d20" d="M6.6 10.8a15.1 15.1 0 0 0 6.6 6.6l2.2-2.2a1 1 0 0 1 1-.25 11.4 11.4 0 0 0 3.6.57 1 1 0 0 1 1 1V20a1 1 0 0 1-1 1A17 17 0 0 1 3 4a1 1 0 0 1 1-1h3.5a1 1 0 0 1 1 1c0 1.25.2 2.45.57 3.57a1 1 0 0 1-.25 1z"/></svg>
      </span>
      <span class="icon-badge" aria-label="Email">
        <svg viewBox="0 0 24 24"><rect x="2" y="5" width="20" height="14" rx="2" fill="#1d1d20"/><path d="M3 6l9 7 9-7" stroke="#d9a12e" stroke-width="2" fill="none"/></svg>
      </span>
      <span class="icon-badge" aria-label="Website">
        <svg viewBox="0 0 24 24" fill="none" stroke="#1d1d20" stroke-width="2"><circle cx="12" cy="12" r="9"/><path d="M3 12h18M12 3c3 3.5 3 14.5 0 18M12 3c-3 3.5-3 14.5 0 18"/></svg>
      </span>
    </div>

    <ul class="contact-list">
      <li>0782 225 4961</li>
      <li>info@renwick-tolliver.co.uk</li>
      <li>www.renwick-tolliver.co.uk</li>
    </ul>

    <address class="address" style="font-style: normal;">
      <span class="icon-badge" aria-label="Location">
        <svg viewBox="0 0 24 24"><path fill="#1d1d20" d="M12 2a7 7 0 0 0-7 7c0 5 7 13 7 13s7-8 7-13a7 7 0 0 0-7-7zm0 9.5A2.5 2.5 0 1 1 12 6.5a2.5 2.5 0 0 1 0 5z"/></svg>
      </span>
      Calder Road, Ashworth<br>Fernmouth, FM4 2QT
    </address>
  </section>

</main>
</body>
</html>
```